Business Cards Design for the electrical wholesaler: clean bold dynamic :)

We need a business card design that would follow our latest brand guidelines. As an electrical wholesaler we want to bring a fresh look and feel into the industry. The design should be clean bold and dynamic. It should come alive with the renewed energy of our green colour. Our grey colour should keep things balanced and complement the notion of maturity and responsibility. We employ Lato as a corporate font however are not bound by this font and we’re open to interpretation here.

Target Market(s)

Electrical contractors

Industry/Entity Type

Business

Contact Information for Business Card

Logo
Name & Surname: Halyna Dorosh
Job Title: Director of Marketing
Email: halya.dorosh@quillmail.example
Cell phone: XXX.XXX.XXXX
Address: 20517 - 87 Ave. Edmonton, AB, Canada. T6K 4N8
Business Phone: 780.555.0184
Website: www.brovix.example

Font styles to use
Other font styles liked:
• Lato

Requirements
Must have
• Logo & website
Nice to have
• Brand elements - some of them you may find in the attached Brand Guidelines (e.g. three lines on the background signifying "W")

```html
<!DOCTYPE html>
<html lang="en">
<head>
<meta charset="utf-8">
<title>Brovix business cards</title>
<link rel="stylesheet" href="https://fonts.googleapis.com/css2?family=Roboto:wght@300;400;700&display=swap">
<style>
  :root {
    --brand-green: #6cc417;
    --brand-grey: #3e4144;
    --ink: #2b2d2f;
    --paper: #ffffff;
    --backdrop: #e8e5e0;
  }
  * { box-sizing: border-box; margin: 0; padding: 0; }
  html, body { width: 1200px; height: 800px; overflow: hidden; }
  body {
    background: var(--backdrop);
    font-family: "Roboto", Arial, sans-serif;
    color: var(--ink);
    position: relative;
  }
  .card {
    position: absolute;
    top: 252px;
    width: 520px;
    height: 297px;
    border-radius: 4px;
    box-shadow: 0 10px 28px rgba(0,0,0,0.18);
    overflow: hidden;
  }
  /* Front */
  .card-front { left: 50px; background: var(--paper); }
  .card-front .accent-band {
    position: absolute; left: 0; top: 0; bottom: 0; width: 14px;
    background: var(--brand-green);
  }
  .card-front .name-marker {
    position: absolute; left: 14px; top: 64px;
    width: 0; height: 0;
    border-top: 11px solid transparent;
    border-bottom: 11px solid transparent;
    border-left: 11px solid var(--brand-grey);
  }
  .identity { position: absolute; left: 50px; top: 56px; }
  .identity .person-name {
    font-weight: 300; font-size: 24px; letter-spacing: 0.2px; color: var(--ink);
  }
  .identity .job-title {
    font-weight: 700; font-size: 12.5px; margin-top: 3px; color: var(--ink);
  }
  .brand-name {
    font-family: "Roboto", Arial, sans-serif;
    font-weight: 400;
    display: flex; align-items: center; gap: 10px;
  }
  .brand-name .brand-dot { border-radius: 50%; background: var(--brand-green); }
  .card-front .brand-name {
    position: absolute; right: 40px; top: 50px;
    font-size: 44px; color: var(--brand-grey);
  }
  .card-front .brand-dot { width: 18px; height: 18px; }
  .contact-list {
    position: absolute; left: 50px; bottom: 40px;
    list-style: none; font-size: 12.5px; line-height: 1.45;
  }
  .contact-list li { display: flex; align-items: flex-start; gap: 9px; }
  .contact-list svg { flex: 0 0 11px; width: 11px; height: 12px; margin-top: 3px; }
  /* Back */
  .card-back { left: 630px; background: var(--brand-grey); }
  .card-back .brand-name {
    position: absolute; left: 0; right: 0; top: 92px;
    justify-content: center;
    font-size: 58px; color: #ffffff;
  }
  .card-back .brand-dot { width: 24px; height: 24px; }
  .card-back .website {
    position: absolute; left: 0; right: 0; top: 218px;
    text-align: center; font-size: 12.5px; letter-spacing: 4px;
    color: var(--brand-green);
  }
</style>
</head>
<body>
  <section class="card card-front" aria-label="Business card front">
    <div class="accent-band"></div>
    <div class="name-marker"></div>
    <div class="identity">
      <p class="person-name">Halyna Dorosh</p>
      <p class="job-title">Manager Finance</p>
    </div>
    <div class="brand-name"><span class="brand-dot"></span>brovix</div>
    <ul class="contact-list">
      <li>
        <svg viewBox="0 0 11 12"><path d="M5.5 0.5a3.8 3.8 0 0 0-3.8 3.8c0 2.8 3.8 7.2 3.8 7.2s3.8-4.4 3.8-7.2A3.8 3.8 0 0 0 5.5 0.5z" fill="#6cc417"/><circle cx="5.5" cy="4.3" r="1.4" fill="#fff"/></svg>
        <span>20517 - 87 Ave. Edmonton, AB<br>T6K 4N8</span>
      </li>
      <li>
        <svg viewBox="0 0 11 12"><rect x="2.5" y="0.8" width="6" height="10.4" rx="1" fill="none" stroke="#6cc417" stroke-width="1.3"/><circle cx="5.5" cy="9.3" r="0.7" fill="#6cc417"/></svg>
        <span>780.555.0184</span>
      </li>
      <li>
        <svg viewBox="0 0 11 12"><rect x="0.8" y="3" width="9.4" height="7" fill="none" stroke="#6cc417" stroke-width="1.2"/><path d="M0.8 3l4.7 4 4.7-4" fill="none" stroke="#6cc417" stroke-width="1.2"/></svg>
        <span>hello@brovix.example</span>
      </li>
    </ul>
  </section>

  <section class="card card-back" aria-label="Business card back">
    <div class="brand-name"><span class="brand-dot"></span>brovix</div>
    <p class="website">www.brovix.example</p>
  </section>
</body>
</html>
```